Equine Podcast Cover Art Design

We need catchy cover art for a horse related podcast "Ride Onward Together"
Brief show description"
Whether you want to ride to experience horses, develop yourself to the next level as a horseman/horsewoman or ride to improve your physical and mental health, we are committed to helping you Ride Onward TogetherĀ®. Join us as we explore the nuance of equine management and sports as well as interview industry professionals to provide you with the knowledge necessary to be a better partner for your equine friends.
I have uploaded two existing logos we use for various purposes to give you an idea of existing style.
Target Market(s)
Horse owners and other equine professionals
Look and feel
Each slider illustrates characteristics of the customer's brand and the style your logo design should communicate.

```html
<!DOCTYPE html>
<html lang="en">
<head>
<meta charset="utf-8">
<title>Ride Onward Together – Podcast Cover</title>
<link href="https://fonts.googleapis.com/css2?family=Bebas+Neue&display=swap" rel="stylesheet">
<style>
  :root {
    --navy: #37396f;
    --red: #b72435;
    --paper: #f4f4f4;
    --arena-light: #fafafa;
    --arena-mid: #dedede;
    --flag-red: #c8283c;
    --flag-navy: #2b2f6a;
    --horse-bay: #8a4a22;
    --horse-dark: #4a2412;
    --rider-dark: #23273a;
  }
  html, body {
    margin: 0;
    padding: 0;
    width: 1200px;
    height: 1200px;
    overflow: hidden;
    background: var(--paper);
  }
  .cover {
    position: relative;
    width: 1200px;
    height: 1200px;
    overflow: hidden;
    font-family: "Bebas Neue", "Oswald", sans-serif;
  }
  .arena-backdrop {
    position: absolute;
    inset: 0;
    background: linear-gradient(180deg, var(--arena-light) 0%, var(--arena-mid) 45%, #eeeeee 70%, #f3f3f3 100%);
  }
  .flag-area {
    position: absolute;
    left: 199px;
    top: 0;
    width: 1001px;
    height: 440px;
  }
  .flag-area svg { width: 100%; height: 100%; display: block; }
  .rider-photo {
    position: absolute;
    left: 600px;
    top: 78px;
    width: 600px;
    height: 712px;
    border-radius: 220px 0 0 160px;
    background:
      radial-gradient(ellipse 55% 45% at 85% 20%, var(--rider-dark) 0%, rgba(35,39,58,0) 100%),
      radial-gradient(ellipse 70% 60% at 45% 45%, var(--horse-bay) 0%, var(--horse-dark) 100%);
  }
  .farm-mark {
    position: absolute;
    left: 100px;
    top: 198px;
    display: flex;
    align-items: center;
    gap: 12px;
  }
  .farm-mark .dot {
    width: 26px;
    height: 26px;
    border-radius: 50%;
    background: var(--red);
  }
  .farm-mark .name {
    font-size: 38px;
    color: var(--navy);
    letter-spacing: 1px;
    line-height: 1;
  }
  .title-line {
    position: absolute;
    margin: 0;
    line-height: 1;
    white-space: nowrap;
    font-weight: 400;
    transform-origin: left top;
  }
  .title-ride, .title-onward {
    left: 94px;
    font-size: 207px;
    color: var(--navy);
  }
  .title-ride { top: 388px; }
  .title-onward { top: 552px; transform: scaleX(0.885); }
  .title-together {
    left: 100px;
    top: 760px;
    font-size: 300px;
    color: var(--red);
    transform: scale(0.975, 1.42);
  }
  .title-together .reg {
    font-size: 34px;
    vertical-align: top;
    position: relative;
    top: 28px;
    margin-left: 14px;
    display: inline-block;
    transform: scaleY(0.7);
    font-family: Arial, sans-serif;
  }
</style>
</head>
<body>
<main class="cover">
  <div class="arena-backdrop" role="img" aria-label="Soft black and white photo of an indoor riding arena with raked sand"></div>

  <div class="flag-area" role="img" aria-label="Photo of a waving American flag draped across the top of the cover">
    <svg viewBox="0 0 1001 440" preserveAspectRatio="none">
      <defs>
        <linearGradient id="flagTone" x1="0" y1="0" x2="1" y2="1">
          <stop offset="0" stop-color="#2b2f6a"/>
          <stop offset="0.35" stop-color="#2b2f6a"/>
          <stop offset="0.4" stop-color="#c8283c"/>
          <stop offset="0.7" stop-color="#e9c9cd"/>
          <stop offset="1" stop-color="#c8283c"/>
        </linearGradient>
      </defs>
      <path d="M0 0 H1001 V230 C900 260 820 300 760 440 C700 340 560 190 420 150 C260 105 120 60 0 0 Z" fill="url(#flagTone)"/>
    </svg>
  </div>

  <div class="rider-photo" role="img" aria-label="Cut-out photo of a bay horse jumping with a rider in a dark show jacket and helmet"></div>

  <div class="farm-mark">
    <span class="dot"></span>
    <span class="name">LINDEN HOLLOW FARM</span>
  </div>

  <h1 class="title-line title-ride">RIDE</h1>
  <p class="title-line title-onward">ONWARD</p>
  <p class="title-line title-together">TOGETHER<span class="reg">®</span></p>
</main>
</body>
</html>
```